Bright and beautiful business card for a coach

I'm a personal and business coach based in Perth, Australia. I need a business card that whilst subtle and elegant, will stand out and appeal on a table full of cards.

My business name is Fern Mentoring and the business card must represent the warmth and brightness implied in the name, without being gimmicky. It must have a warmth and appeal and be easy to read.

I prefer clean, minimalist designs.

It must align with the feel of my website and socials: https://www.fernmentoring-example.com.au/
https://www.instagram.com/fernmentoringau/
https://www.facebook.com/fernmentoringau
Updates

Hi Designers Thank you so much for taking the time to submit designs. I wonder if I could have explained myself a little better. Most of the designs that have been submitted look rather formal and many have quite corporate looking embellishments on them (to my eye). I would like softer, warmer, more organic. I’m open to people playing about and being more abstract, using softer embellishments (e.g the line drawing flowers and grasses I’ve used in my socials) incorporating other colours from my palette or like the social icons in my email signature (in PDF), perhaps playing with size/oversize, playing with the bleed. Please don’t be constrained by what I’ve already done, it merely needs to compliment. I’m sorry if I’m not using the right words or have led you astray. I’m no designer, but I’ve done my website, socials, email signature etc all myself (my logo was a design contest) and I was really hoping for my business card to be something more creative than I could have made with a template. Reminder: No black cards/sides please. Thank you 😊

Target Market(s)

Individuals, most likely but not all female. Creative thinkers. Likely professionals.

Industry/Entity Type

Business & Personal Coach

Contact Information for Business Card

(Fern Mentoring Logo) Name: Greta Pellham; Title: Business & Personal Coach; Phone number: +61 (0)458 913307; Email: greta@fernmentoring-example.com.au; Website: https://fernmentoring-example.com.au; Social icons for Facebook, Instagram & LinkedIn: @fernmentoringAU. Optional strapline: "A steady partner to help you find your own clear way"

Font styles to use
Sans Serif

Colors
00AB8E
00BBA5
67D7C9
C6EFE9
E9F9F6
59FF00
82FF00
B8FF75
E3FFCB
F4FFEA
FFC000
F8CF3A
FAE287
FDF2CF
FEFAEE

Requirements
Must have
• Must align with feel of my website and socials. Must have a pop of #FFC000 (possibly whole of one side, or at least a block). Bright or white background. Easy to read.
Nice to have
• Possibly incorporate the sunshine/grass picture I have used in website and socials - will upload.
Should not have
• Must not be black or dark. Not impersonal or corporate looking.

```html
<!DOCTYPE html>
<html lang="en">
<head>
<meta charset="utf-8">
<title>Fern Mentoring – Business Card</title>
<link rel="stylesheet" href="https://fonts.googleapis.com/css2?family=Lato:wght@400;700&family=Mrs+Saint+Delafield&display=swap">
<style>
  :root {
    --stage: #d3d6d8;
    --card-white: #ffffff;
    --sun: #ffc000;
    --lime: #b8d43a;
    --teal: #67b8c9;
    --teal-text: #8cc3cc;
    --ink: #4a4a4a;
    --grey: #8a8a8a;
    --grass-dark: #2f4d1c;
    --grass-mid: #5f8f2c;
    --grass-light: #a9c86a;
    --haze: #efe2cf;
  }
  * { margin: 0; padding: 0; box-sizing: border-box; }
  html, body {
    width: 1200px; height: 928px; overflow: hidden;
    background: var(--stage);
    font-family: "Lato", sans-serif;
  }
  .canvas { position: relative; width: 1200px; height: 928px; }

  .card {
    position: absolute;
    width: 560px; height: 320px;
    border-radius: 22px;
    overflow: hidden;
    box-shadow: 0 10px 24px rgba(0,0,0,0.18);
  }

  /* Front */
  .card--front { left: 80px; top: 110px; }
  .front-photo {
    position: absolute; inset: 0;
    background:
      radial-gradient(circle at 58% 12%, var(--haze) 0%, rgba(239,226,207,0) 38%),
      linear-gradient(180deg, var(--grass-light) 0%, var(--grass-mid) 45%, var(--grass-dark) 100%);
  }
  .front-brand {
    position: absolute; left: 0; right: 0; top: 138px;
    display: flex; align-items: center; justify-content: center; gap: 14px;
  }
  .front-brand .mark {
    width: 34px; height: 34px; border-radius: 50%;
    background: var(--sun);
  }
  .front-brand .name {
    font-size: 32px; font-weight: 400; letter-spacing: 2px;
    color: var(--card-white); line-height: 1;
  }

  /* Back */
  .card--back { left: 560px; top: 500px; background: var(--card-white); }
  .holder-name {
    position: absolute; left: 38px; top: 26px;
    font-family: "Mrs Saint Delafield", cursive;
    font-size: 52px; color: var(--sun); line-height: 1;
  }
  .holder-title {
    position: absolute; left: 40px; top: 92px;
    font-size: 14px; color: var(--ink);
  }
  .brand {
    position: absolute; right: 36px; top: 58px;
    display: flex; align-items: center; gap: 10px;
  }
  .brand .mark {
    width: 22px; height: 22px; border-radius: 50%;
    background: var(--sun);
  }
  .brand .name {
    font-size: 24px; font-weight: 400; letter-spacing: 1.5px;
    color: var(--grey); line-height: 1;
  }
  .contact {
    position: absolute; left: 40px; top: 168px;
    font-size: 13.5px; line-height: 20px; color: var(--ink);
    list-style: none;
  }
  .socials {
    display: flex; align-items: center; gap: 5px; margin-top: 4px;
  }
  .socials .dot { width: 15px; height: 15px; border-radius: 3px; }
  .dot--a { background: var(--sun); }
  .dot--b { background: var(--lime); }
  .dot--c { background: var(--teal); }
  .socials .handle { color: var(--teal-text); margin-left: 4px; }
  .strapline {
    position: absolute; left: 40px; bottom: 26px;
    font-size: 14px; font-weight: 700; color: var(--sun);
  }
</style>
</head>
<body>
<main class="canvas">
  <section class="card card--front">
    <div class="front-photo" role="img" aria-label="Sunlit close-up photograph of green grass with soft bokeh"></div>
    <div class="front-brand">
      <span class="mark"></span>
      <span class="name">Fern Mentoring</span>
    </div>
  </section>

  <section class="card card--back">
    <p class="holder-name">Greta Pellham</p>
    <p class="holder-title">Business &amp; Personal Coach</p>
    <div class="brand">
      <span class="mark"></span>
      <span class="name">Fern Mentoring</span>
    </div>
    <ul class="contact">
      <li>+61 (0)458 913307</li>
      <li>greta@fernmentoring-example.com.au</li>
      <li>www.fernmentoring-example.com.au</li>
      <li class="socials">
        <span class="dot dot--a"></span>
        <span class="dot dot--b"></span>
        <span class="dot dot--c"></span>
        <span class="handle">@fernmentoringAU</span>
      </li>
    </ul>
    <p class="strapline">A steady partner to help you find your own clear way</p>
  </section>
</main>
</body>
</html>
```